New Innovative Counselling and psychotherapy Service needs Business Card design

Keep it simple and professional. On one side, just company name and logo (perhaps in all blue) and maybe a tag line.

On other side (all white) my name and Qualifications in centre

Industry/Entity Type

Health And Wellness

Contact Information for Business Card

Dara Whelby
Counsellor & Psychotherapist
BSc (Psychol.), BA, Dip. (Couns. & Psych.), PG.Cert (CBT), FGTrK, ONRE

I will also require Mobile no, Email and web site address of which I'll pass on to final designer.

Font styles to use
Sans Serif

Requirements
Must have
• My Logo Only and please use the colours in logo that is in it.
Should not have
• Any other images

```html
<!DOCTYPE html>
<html lang="en">
<head>
<meta charset="utf-8">
<title>Thrive Lane – Business Card</title>
<link rel="stylesheet" href="https://fonts.googleapis.com/css2?family=Arimo:wght@400;700&display=swap">
<style>
  :root {
    --backdrop: #c9c9c9;
    --sky: #45b3ec;
    --leaf: #8fd152;
    --paper: #f1f1f1;
    --charcoal: #333333;
    --ink: #3a3a3a;
    --white: #ffffff;
  }
  * { margin: 0; padding: 0; box-sizing: border-box; }
  html, body { width: 1200px; height: 960px; overflow: hidden; }
  body {
    background: var(--backdrop);
    font-family: "Arimo", Arial, sans-serif;
    position: relative;
  }
  .card {
    position: absolute;
    width: 600px;
    height: 342px;
    border-radius: 18px;
    overflow: hidden;
  }
  .card-front { left: 322px; top: 110px; background: var(--paper); }
  .card-back { left: 320px; top: 493px; background: var(--charcoal); }

  .wave { position: absolute; inset: 0; }

  .holder { position: absolute; left: 31px; top: 25px; color: var(--white); }
  .holder-name { font-size: 24px; font-weight: 700; line-height: 1.1; }
  .holder-role { font-size: 14px; margin-top: 6px; }
  .holder-quals { font-size: 11.5px; line-height: 1.2; margin-top: 2px; }

  .contact-list { list-style: none; margin-top: 10px; }
  .contact-list li {
    display: flex; align-items: center; gap: 7px;
    font-size: 14px; line-height: 19.5px;
  }
  .contact-list svg { width: 13px; height: 13px; fill: var(--white); flex: none; }

  .brand { position: absolute; display: flex; align-items: center; }
  .brand-front { left: 308px; top: 250px; gap: 20px; }
  .brand-dot { width: 48px; height: 48px; border-radius: 50%; background: var(--sky); }
  .brand-name-front { font-size: 25px; color: var(--ink); }

  .back-lockup {
    position: absolute; left: 292px; top: 242px; width: 280px;
    text-align: center; color: var(--white);
  }
  .brand-name-back { font-size: 32px; }
  .tagline { font-size: 14px; line-height: 18px; margin-top: 6px; }
</style>
</head>
<body>
  <section class="card card-front">
    <svg class="wave" viewBox="0 0 600 342" aria-hidden="true">
      <path fill="var(--sky)" d="M0,0 H600 V28 C520,18 440,50 370,125 C300,200 240,245 160,245 C95,245 45,222 0,195 Z"/>
      <path fill="none" stroke="var(--sky)" stroke-width="4" d="M0,225 C60,250 120,258 180,252 C260,240 310,165 380,95 C450,30 530,18 600,32"/>
      <path fill="none" stroke="var(--leaf)" stroke-width="7" d="M150,258 C250,245 320,170 390,105 C460,45 535,35 600,48"/>
    </svg>

    <div class="holder">
      <h1 class="holder-name">Dara Whelby</h1>
      <p class="holder-role">Counsellor &amp; Psychotherapist</p>
      <p class="holder-quals">BSc (Psychol.), BA, Dip. (Couns. &amp; Psych.)<br>PG.Cert (CBT), FGTrK,</p>
      <ul class="contact-list">
        <li><svg viewBox="0 0 16 16"><path d="M4 0h8a1 1 0 0 1 1 1v14a1 1 0 0 1-1 1H4a1 1 0 0 1-1-1V1a1 1 0 0 1 1-1zm1 2v10h6V2zm3 11a1 1 0 1 0 0 2 1 1 0 0 0 0-2z"/></svg>555 012 3478</li>
        <li><svg viewBox="0 0 16 16"><path d="M0 3h16v10H0zm1.5 1.2L8 9l6.5-4.8V4h-13z"/></svg>dara@Thrivelane.com</li>
        <li><svg viewBox="0 0 16 16"><circle cx="8" cy="8" r="7.5"/></svg>www.Thrivelane.com</li>
      </ul>
    </div>

    <div class="brand brand-front">
      <span class="brand-dot"></span>
      <span class="brand-name-front">Thrive Lane</span>
    </div>
  </section>

  <section class="card card-back">
    <div class="back-lockup">
      <p class="brand-name-back">Thrive Lane</p>
      <p class="tagline">Caring For Your Psychological Well-Being<br>Is Our Top Priority</p>
    </div>
  </section>
</body>
</html>
```